Advanced Therapeutic Massage Therapist

I need a business card advertising my massage services as an advanced therapeutic massage therapist. I offer advanced therapeutic massage, swedish and deep tissue. I want to create a simple, professional and feminine card. I like bright colours and creativity.

I prefer a bold and experimental approach rather than something status-quo. A card to suggest therapeutic healing through dynamic massage. Motifs, shapes or layout which suggest movement and flow.
Updates

Target Market(s)

Everybody!

Industry/Entity Type

Health And Wellness

Contact Information for Business Card

The card should include:
My name, logo, services offered and my contact details.

Sláine Dunleavy
Massage Therapist

- Swedish - Deep Tissue - Advanced Therapeutic

Phone: (+353) 87 216 4093
Email: regenerate@slainedunleavy-example.com
Website: www.slainedunlevy-example.com

Font styles to use
Serif
Sans Serif
Decorative
Script

Colors

Designer to choose colors to be used in the design.

Requirements
Must have
• An example may contain something like this, yet concise:
• "Sláine Dunleavy
• Massage Therapist
• - Swedish - Deep Tissue - Advanced Therapeutic"
Nice to have
• This sentence is optional:
• Imagery such as a logo or symbol. I have attached a file containing a logo I had produced however the name is incorrect now as it is "Sláine" not "Nelly". It could be edited to change it to Sláine.
• I have sent the file as .psd .jpg. .pdf and .png
• I like when the card conveys energy, movement, pressure points, flow etc.
• I just like the designer to follow their own style and ideas. I like bright colours but must have a lot of a base colour to offset it. I really prefer them to follow their own inspiration. That is my preference.
Should not have
• Pine trees, non-native trees to Britain and Ireland, exotic flowers or animals that are not native to Britain and Ireland.
• I don't like brown as the background colour of the card.
• The cars shouldn't look like a wedding invitation i.e too many floral type designs.

```html
<!DOCTYPE html>
<html lang="en">
<head>
<meta charset="utf-8">
<title>Sláine Dunleavy – Massage Therapist Business Card</title>
<link href="https://fonts.googleapis.com/css2?family=Questrial&display=swap" rel="stylesheet">
<style>
  :root {
    --backdrop: #2a2a2a;
    --card: #0b0b0b;
    --card-edge: #1c1c1c;
    --gold: #f2b93b;
    --gold-bright: #ffd467;
    --gold-deep: #b07a1e;
    --ink: #f4f4f4;
  }
  * { margin: 0; padding: 0; box-sizing: border-box; }
  html, body {
    width: 1200px; height: 930px; overflow: hidden;
    background: var(--backdrop);
    font-family: "Questrial", "Helvetica Neue", Arial, sans-serif;
  }
  .sheet {
    width: 1200px; height: 930px;
    display: flex; flex-direction: column; align-items: center; justify-content: center;
    gap: 34px;
  }
  .card {
    position: relative;
    width: 800px; height: 420px;
    background: linear-gradient(135deg, #161616 0%, var(--card) 55%, #050505 100%);
    border: 1px solid var(--card-edge);
    border-radius: 22px;
    box-shadow: 0 14px 30px rgba(0,0,0,.45);
    overflow: hidden;
    color: var(--ink);
  }
  .flow {
    position: absolute; inset: 0; width: 100%; height: 100%;
    pointer-events: none;
  }
  .emblem-fill {
    border-radius: 50%;
    background: radial-gradient(circle at 40% 35%, var(--gold-bright) 0%, var(--gold) 40%, var(--gold-deep) 100%);
    box-shadow: 0 0 30px rgba(242,185,59,.25);
  }

  /* Front */
  .front .brand {
    position: absolute; left: 0; right: 0; top: 62px;
    display: flex; flex-direction: column; align-items: center;
  }
  .front .brand-mark { width: 170px; height: 170px; }
  .brand-name {
    margin-top: 22px;
    font-size: 30px; color: var(--ink); letter-spacing: .5px; line-height: 1.1;
  }
  .brand-role {
    margin-top: 4px;
    font-size: 15px; letter-spacing: 2px; color: var(--ink);
  }
  .tagline {
    position: absolute; left: 0; right: 0; bottom: 40px;
    text-align: center; font-size: 19px; letter-spacing: .4px;
  }

  /* Back */
  .back .emblem {
    position: absolute; left: 100px; top: 100px;
    width: 220px; height: 220px;
  }
  .back .divider {
    position: absolute; left: 375px; top: 80px;
    width: 2px; height: 260px; background: var(--gold);
  }
  .details {
    position: absolute; left: 405px; top: 78px; right: 24px;
  }
  .details .name {
    font-size: 34px; font-weight: 400; color: var(--gold); line-height: 1; white-space: nowrap;
  }
  .details .role {
    margin-top: 8px; font-size: 17px; letter-spacing: .6px;
  }
  .contact { list-style: none; margin-top: 24px; }
  .contact li {
    display: flex; align-items: center; gap: 11px;
    font-size: 17px; line-height: 1.6; white-space: nowrap;
  }
  .contact svg { width: 16px; height: 16px; flex: none; }
  .services { list-style: none; margin-top: 18px; }
  .services li {
    display: flex; align-items: center; gap: 14px;
    font-size: 18px; line-height: 1.5; text-transform: uppercase;
  }
  .services li::before {
    content: ""; width: 10px; height: 10px; border-radius: 50%;
    background: var(--gold); flex: none;
  }
</style>
</head>
<body>
  <main class="sheet">
    <section class="card front" aria-label="Card front">
      <svg class="flow" viewBox="0 0 800 420" aria-hidden="true">
        <path d="M-20 360 C 150 300, 260 420, 420 370 S 700 300, 820 340" fill="none" stroke="#f2b93b" stroke-opacity=".22" stroke-width="2"/>
        <path d="M-20 385 C 170 330, 280 440, 440 395 S 710 330, 820 365" fill="none" stroke="#f2b93b" stroke-opacity=".12" stroke-width="1.5"/>
      </svg>
      <div class="brand">
        <div class="brand-mark emblem-fill" role="img" aria-label="Round gold tree-of-life emblem"></div>
        <div class="brand-name">Sláine Dunleavy</div>
        <div class="brand-role">massage therapist</div>
      </div>
      <p class="tagline">ATMC qualified specialising in advanced therapeutic and deep tissue massage.</p>
    </section>

    <section class="card back" aria-label="Card back">
      <svg class="flow" viewBox="0 0 800 420" aria-hidden="true">
        <path d="M-20 60 C 120 20, 220 110, 360 50" fill="none" stroke="#f2b93b" stroke-opacity=".2" stroke-width="2"/>
        <path d="M-20 380 C 110 340, 230 420, 360 370" fill="none" stroke="#f2b93b" stroke-opacity=".2" stroke-width="2"/>
      </svg>
      <div class="emblem emblem-fill" role="img" aria-label="Round gold tree-of-life emblem"></div>
      <div class="divider" aria-hidden="true"></div>
      <div class="details">
        <h1 class="name">Sláine Dunleavy</h1>
        <p class="role">MASSAGE THERAPIST</p>
        <ul class="contact">
          <li>
            <svg viewBox="0 0 24 24" fill="none" stroke="#f2b93b" stroke-width="2.2" stroke-linecap="round" stroke-linejoin="round" aria-hidden="true">
              <path d="M22 16.9v3a2 2 0 0 1-2.2 2 19.8 19.8 0 0 1-8.6-3.1 19.5 19.5 0 0 1-6-6A19.8 19.8 0 0 1 2.1 4.2 2 2 0 0 1 4.1 2h3a2 2 0 0 1 2 1.7c.1.9.4 1.8.7 2.7a2 2 0 0 1-.5 2.1L8 9.8a16 16 0 0 0 6 6l1.3-1.3a2 2 0 0 1 2.1-.4c.9.3 1.8.6 2.7.7a2 2 0 0 1 1.7 2z"/>
            </svg>
            (+353) 87 216 4093
          </li>
          <li>
            <svg viewBox="0 0 24 24" fill="none" stroke="#f2b93b" stroke-width="2.2" stroke-linecap="round" stroke-linejoin="round" aria-hidden="true">
              <rect x="2" y="5" width="20" height="14" rx="2"/><path d="M2 7l10 6 10-6"/>
            </svg>
            regenerate@slainedunleavy-example.com
          </li>
          <li>
            <svg viewBox="0 0 24 24" fill="none" stroke="#f2b93b" stroke-width="2.2" stroke-linecap="round" stroke-linejoin="round" aria-hidden="true">
              <circle cx="12" cy="12" r="10"/><path d="M2 12h20M12 2a15 15 0 0 1 0 20M12 2a15 15 0 0 0 0 20"/>
            </svg>
            www.slainedunlevy-example.com
          </li>
        </ul>
        <ul class="services">
          <li>Swedish</li>
          <li>Deep Tissue</li>
          <li>Advanced Therapeutic</li>
        </ul>
      </div>
    </section>
  </main>
</body>
</html>
```